High-end law practice specializing in closely held business succession planning and complex estates

Solo practitioner whose practice specializes in high-net worth, complex estate planning needs muliple versions of letterhead black and white, please. Letterhead should incorporate slogan, "Protecting your family business is my business," for one and "Complex Estate Planning"; third with no slogan. All for The Law Office of Marcy Lynn Pettibone, PC, 418 Cedar Hollow Ln., Newport News, Virginia 23648, Tel. 757-555-0142 Fax tbd email: marcy@mlplawgroup.example; Marcy Lynn Pettibone, Esq., principal, licensed in VA, NY, DC
Updates

Project Deadline Extended
Reason: My internet service went down and I can only view designs on my smart phone -- it's just too hard to review. So sorry! Working with my ISP now. Please be patient!

Target Market(s)

High net worth clients with complex estate planning needs, family businesses, family farmers, family foresters -- people with unique estate/succession planning needs who need a specialist who understands them.

Industry/Entity Type

Business

Font styles to use
Script

Requirements
Must have
• A high-end look and feel, connoting trustworthiness, special knowledge, and expertise.

```html
<!DOCTYPE html>
<html lang="en">
<head>
<meta charset="utf-8">
<title>The Law Office of Marcy Lynn Pettibone, PC — Letterhead</title>
<link href="https://fonts.googleapis.com/css2?family=Libre+Baskerville:wght@700&family=Arimo:wght@400;700&family=Open+Sans:wght@400;600&family=Dancing+Script:wght@500&display=swap" rel="stylesheet">
<style>
  :root {
    --backdrop: #e9e9e9;
    --paper: #ffffff;
    --ink: #1a1a1a;
    --body-ink: #3a3a3a;
    --band: #000000;
    --band-text: #ffffff;
    --signature: #2a2f8f;
    --rule: #222222;
  }
  * { box-sizing: border-box; margin: 0; padding: 0; }
  html, body { width: 1200px; height: 795px; overflow: hidden; }
  body { background: var(--backdrop); position: relative; }

  .letterhead {
    position: absolute; left: 320px; top: 15px;
    width: 560px; height: 765px;
    background: var(--paper);
    box-shadow: 0 2px 10px rgba(0,0,0,.12);
    color: var(--body-ink);
    font-family: "Arimo", Arial, sans-serif;
    overflow: hidden;
  }

  .firm-name {
    position: absolute; left: 38px; top: 50px;
    font-family: "Libre Baskerville", Georgia, serif;
    font-weight: 700; font-size: 16px; line-height: 1.2;
    letter-spacing: .5px; text-transform: uppercase; color: var(--ink);
  }
  .header-rule {
    position: absolute; left: 38px; right: 232px; top: 99px;
    height: 1px; background: var(--rule);
  }
  .slogan-band {
    position: absolute; right: 0; top: 90px; width: 240px; height: 18px;
    background: var(--band); color: var(--band-text);
    border-radius: 9px 0 0 9px;
    font-family: "Open Sans", Arial, sans-serif; font-size: 9px;
    display: flex; align-items: center; padding-left: 12px; white-space: nowrap;
  }
  .contact {
    position: absolute; right: 16px; top: 38px;
    font-family: "Open Sans", Arial, sans-serif; font-size: 8px;
    line-height: 14px; text-align: right; color: var(--ink);
  }
  .contact li { list-style: none; display: flex; justify-content: flex-end; align-items: center; gap: 5px; }
  .contact svg { width: 9px; height: 9px; fill: var(--ink); }

  .letter-body { position: absolute; left: 62px; right: 62px; top: 150px; font-size: 8.6px; line-height: 1.3; }
  .date { margin-bottom: 12px; }
  .recipient { margin-bottom: 12px; }
  .salutation { font-weight: 700; margin-bottom: 12px; color: var(--ink); }
  .letter-body p.para { margin-bottom: 11px; text-align: justify; }
  .closing { margin-top: 20px; }
  .signature {
    font-family: "Dancing Script", cursive; font-size: 25px;
    color: var(--signature); line-height: 1.1; margin: 2px 0 2px 18px;
  }
  .signer { margin-left: 36px; }

  .footer-rule {
    position: absolute; left: 200px; right: 38px; bottom: 64px;
    height: 1px; background: var(--rule);
  }
  .specialty-band {
    position: absolute; left: 0; bottom: 34px; width: 220px; height: 24px;
    background: var(--band); color: var(--band-text);
    border-radius: 0 12px 12px 0;
    font-family: "Open Sans", Arial, sans-serif; font-size: 11px;
    display: flex; align-items: center; justify-content: flex-end; padding-right: 18px;
  }
  .footer-address {
    position: absolute; right: 38px; bottom: 70px;
    font-family: "Open Sans", Arial, sans-serif; font-size: 8px; font-style: normal;
    line-height: 12px; text-align: right; color: var(--ink);
  }
</style>
</head>
<body>
  <main class="letterhead">
    <h1 class="firm-name">The Law Office<br>of Marcy Lynn Pettibone</h1>
    <div class="header-rule"></div>

    <ul class="contact">
      <li>757-555-0142
        <svg viewBox="0 0 24 24" aria-hidden="true"><path d="M6.6 10.8a15.1 15.1 0 0 0 6.6 6.6l2.2-2.2a1 1 0 0 1 1-.25 11.4 11.4 0 0 0 3.6.57 1 1 0 0 1 1 1V20a1 1 0 0 1-1 1A17 17 0 0 1 3 4a1 1 0 0 1 1-1h3.5a1 1 0 0 1 1 1c0 1.25.2 2.45.57 3.6a1 1 0 0 1-.25 1z"/></svg></li>
      <li>Fax: TBD
        <svg viewBox="0 0 24 24" aria-hidden="true"><path d="M6 2h10v6H6zM3 9h18v9h-3v4H6v-4H3zm5 6v5h8v-5z"/></svg></li>
      <li>marcy@mlplawgroup.example
        <svg viewBox="0 0 24 24" aria-hidden="true"><path d="M2 5h20v14H2zm2 2v.5l8 5 8-5V7l-8 5z"/></svg></li>
    </ul>
    <div class="slogan-band">Protecting Your Family Business is my Business</div>

    <section class="letter-body">
      <p class="date">January 12, 2014</p>
      <p class="recipient">Mr. John Doe<br>President<br>AA Corporation<br>111 Street Name, Suite#<br>City, State, 12345</p>
      <p class="salutation">Dear Mr. John,</p>
      <p class="para">Lorem Ipsum is simply dummy text of the printing and typesetting industry. Lorem Ipsum has been the industry's standard dummy text ever since the 1500s, when an unknown printer took a galley of type and scrambled it to make a type specimen book. It has survived not only five centuries, but also the leap into electronic typesetting, remaining essentially unchanged.</p>
      <p class="para">The standard chunk of Lorem Ipsum used since the 1500s is reproduced below for those interested. Sections 1.10.32 and 1.10.33 from "de Finibus Bonorum et Malorum" by Cicero are also reproduced in their exact original form, accompanied by English versions from the 1914 translation by H. Rackham.</p>
      <p class="para">Lorem Ipsum is simply dummy text of the printing and typesetting industry. Lorem Ipsum has been the industry's standard dummy text ever since the 1500s, when an unknown printer took a galley of type and scrambled it to make a type specimen book. It has survived not only five centuries, but also the leap into electronic typesetting, remaining essentially unchanged. It was popularised in the</p>
      <div class="closing">
        <p>Sincerely Your,</p>
        <p class="signature">your name</p>
        <p class="signer">Name Last Name<br>Company Name</p>
      </div>
    </section>

    <address class="footer-address">
      PC 418 Cedar Hollow Ln.<br>
      Newport News, Virginia 23648,<br>
      Marcy Lynn Pettibone, Esq., principal, licensed in VA, NY, DC
    </address>
    <div class="footer-rule"></div>
    <div class="specialty-band">Complex Estate Planning</div>
  </main>
</body>
</html>
```